Web Design Project

Looking for an eye catching banner page to be used on the website and LinkedIn. We are an Executive Recruiting and HR Consulting service firm with a modern edge. We want to demonstrate through our brand that we are using the latest recruiting trends to find talent and that we are easy to work with- innovative and simple.We typically recruit for Engineers, IT professionals, Accounting and Operation Managers. Our website is www.bluvantatalent.com and it needs a fresh clean look. We love our logo but might want to use the "8" to show the 2 sides of our business or maybe to use the infinity concept or continuous improvement. We like the Green and white colors with accents in gray.

Target Market(s)

Small to mid-sized Business Managers seeking innovation

Industry/Entity Type

Business

Requirements
Must have
• Use of the 8
Long picture on top to be used on LinkedIn and the website top
Clean Simple look- modern font like century gothic
Nice to have
• Smiling face(s)
Layered image of 8 or of photo stock faces
Maybe a modern office so they feel that they walked in to meet us (fyi our office has white chandeliers and green walls that match our logo)
Should not have
• Busy or cluttered feel

```html
<!DOCTYPE html>
<html lang="en">
<head>
<meta charset="utf-8">
<title>Bluvanta – Where strategy meets recruiting</title>
<link rel="stylesheet" href="https://fonts.googleapis.com/css2?family=Questrial&family=Arimo:wght@400;700&display=swap">
<style>
:root{
  --lime:#a9c23f;
  --lime-dark:#8ca332;
  --olive:#8fa336;
  --olive-dark:#7c8f2b;
  --ink:#333638;
  --slate:#5c6166;
  --slate-dark:#4a4f54;
  --line:#d5d7d9;
  --white:#ffffff;
}
*{box-sizing:border-box;margin:0;padding:0}
html,body{width:1000px;height:1200px;overflow:hidden;background:var(--white)}
body{position:relative;font-family:"Arimo",Arial,sans-serif;color:var(--ink)}
.abs{position:absolute}
.heading{font-family:"Questrial","Century Gothic",sans-serif}
.top-rule{left:0;top:0;width:1000px;height:5px;background:var(--lime)}

.brand{left:186px;top:38px}
.brand-name{font-family:"Questrial",sans-serif;font-size:42px;color:var(--lime);display:flex;align-items:center;gap:10px}
.brand-dot{width:26px;height:26px;border-radius:50%;background:var(--lime)}

.quick-links{left:619px;top:30px;width:192px;height:30px;background:#f1f2f2;border:1px solid var(--line);border-radius:4px;font-size:11px;display:flex;align-items:center;justify-content:center;gap:8px;color:var(--ink)}
.quick-links svg{vertical-align:middle;margin-right:3px}
.account-btn{top:70px;width:92px;height:25px;border-radius:3px;background:linear-gradient(#b7d05a,#98b434);color:#fff;font-size:12px;display:flex;align-items:center;justify-content:center;border:1px solid var(--lime-dark)}

.main-nav{left:186px;top:119px;width:625px;height:33px;background:linear-gradient(#7a7f84,#5c6166);display:flex;align-items:center;font-size:10px;color:#fff;white-space:nowrap}
.main-nav .home{width:30px;height:33px;display:flex;align-items:center;justify-content:center}
.main-nav a{padding:0 7px;color:#fff;text-decoration:none}
.main-nav a.active{border-bottom:2px solid #fff;padding-bottom:2px}
.site-search{margin-left:auto;margin-right:6px;width:156px;height:22px;background:#fff;color:#333;font-size:9px;font-weight:700;display:flex;align-items:center;justify-content:space-between;padding:0 6px}

.hero{left:186px;top:160px;width:625px;height:217px;background:linear-gradient(100deg,#e9ebe0 0%,#dfe7c4 35%,#c8d77e 50%,#eef0ec 62%,#d9cbbf 80%,#efe9e3 100%)}
.hero-caption{left:186px;top:340px;width:558px;height:37px;background:rgba(92,97,102,.85);color:#fff;font-size:13px;line-height:16px;padding:3px 10px;font-family:"Questrial",sans-serif}
.hero-arrow{top:256px;width:19px;height:19px;border-radius:50%;background:#fff;border:2px solid var(--lime)}

.intro-title{right:189px;top:385px;font-size:22px;color:var(--slate);font-weight:400}
.intro-rule{left:186px;top:416px;width:625px;height:1px;background:var(--lime)}
.intro-ring{left:202px;top:390px;width:52px;height:52px;border-radius:50%;border:3px solid var(--lime);background:#fff}
.intro-copy{left:186px;top:454px;width:625px;font-size:9.5px;line-height:11.5px}
.intro-copy p{margin-bottom:10px}
.small-btn{height:17px;border-radius:3px;background:linear-gradient(#b7d05a,#94b032);color:#fff;font-size:9px;display:flex;align-items:center;justify-content:center;border:1px solid var(--lime-dark);white-space:nowrap}

.services{left:0;top:542px;width:1000px;height:124px;background:linear-gradient(#e6e7e8,#fafafa 40%,#ededee);border-top:4px solid #d9dadb;border-bottom:4px solid #d9dadb}
.service{top:18px;width:200px;text-align:center;font-size:12px;font-weight:700}
.service .disc{width:74px;height:74px;border-radius:50%;margin:0 auto 10px;background:var(--slate);border:4px solid #9a9ea2;display:flex;align-items:center;justify-content:center}
.service .disc.on{background:var(--lime);border-color:#c8d98a}

.numbers{left:186px;top:683px;width:414px;height:201px;background:#e9eaea;border:1px solid var(--line)}
.numbers-head{height:36px;background:linear-gradient(#9fb83c,#86a02c);color:#fff;font-size:19px;padding:6px 12px}
.stat{left:6px;width:394px;background:#cfd1d2;display:flex;align-items:center;font-size:9.5px;line-height:11px}
.stat .num{width:32px;align-self:stretch;background:var(--slate);color:#fff;display:flex;align-items:center;justify-content:center;font-size:12px;font-weight:700;flex:none}
.stat .txt{padding:0 6px}
.scroll{left:404px;top:45px;width:5px;height:148px;background:#fff;border:1px solid var(--line)}

.testimonials{left:618px;top:683px;width:194px;height:201px;background:#ededee;border:1px solid var(--line);padding:6px 9px;font-size:8.5px;line-height:10.5px}
.testimonials h2{font-family:"Questrial",sans-serif;font-weight:400;font-size:18px;color:var(--lime-dark);margin-bottom:6px}
.testimonials .quote{font-weight:700}
.testimonials cite{display:block;text-align:right;font-style:normal;font-weight:700;color:var(--lime-dark);margin:3px 0 7px}

.social-tab{left:408px;top:910px;width:186px;height:34px;background:var(--slate);border-radius:8px 8px 0 0;display:flex;gap:6px;justify-content:center;align-items:center}
.social-tab i{width:19px;height:19px;border-radius:3px;background:#9fb6d8;display:block}
.band{left:0;top:937px;width:1000px;height:7px;background:var(--slate)}

.footer{left:0;top:944px;width:1000px;height:226px;background:linear-gradient(#9bb03b,var(--olive) 60%,var(--olive-dark))}
.footer h3{font-family:"Questrial",sans-serif;font-weight:400;color:#fff;font-size:15px;border-bottom:1px solid #b6c76c;padding-bottom:5px;margin-bottom:10px}
.footer ul{list-style:none;font-size:9.5px;color:#fff;line-height:17px}
.badge{left:190px;top:1086px;width:104px;height:50px;background:#fff;border-radius:6px;border:2px solid #2a6aa4}
.hub{left:186px;top:1140px;width:108px;height:18px;background:var(--slate);color:#fff;font-size:9px;display:flex;align-items:center;justify-content:center;border-radius:2px}
.contact-row{display:flex;gap:10px;color:#fff;font-size:9px;line-height:11px;margin-bottom:7px;align-items:flex-start}
.contact-row.big{font-size:13px;align-items:center}

.jobs{left:490px;top:966px;width:156px;height:182px;background:#fff;border:1px solid var(--line)}
.jobs-head{height:26px;background:var(--slate);color:#fff;font-family:"Questrial",sans-serif;font-size:13px;display:flex;align-items:center;justify-content:space-between;padding:0 8px}
.jobs ul{list-style:none;padding:8px;font-size:8.5px;font-weight:700;line-height:11px}
.jobs li{margin-bottom:8px}
.fan{left:653px;top:966px;width:159px;height:182px;background:#fff;border:1px solid var(--line);padding:6px;font-size:8px}
.fan-name{font-family:"Questrial",sans-serif;color:var(--lime);font-size:18px;display:flex;align-items:center;gap:6px}
.fan-name i{width:12px;height:12px;border-radius:50%;background:var(--lime);display:block}
.follow{border:1px solid #bbb;border-radius:2px;font-size:8px;padding:1px 4px;background:#f4f4f4;margin-left:6px;color:var(--slate)}
.thumbs{display:grid;grid-template-columns:repeat(4,32px);gap:4px;margin-top:8px}
.thumbs div{width:32px;height:32px;background:linear-gradient(#c7c2bb,#8e8a85)}
.copyright{left:0;top:1170px;width:1000px;height:30px;background:var(--slate-dark);color:#e4e4e4;font-size:8.5px;display:flex;align-items:center;justify-content:center}
</style>
</head>
<body>
<div class="abs top-rule"></div>

<header>
  <div class="abs brand">
    <div class="brand-name"><span>Bluvanta</span><span class="brand-dot"></span></div>
  </div>
  <div class="abs quick-links">
    <span><svg width="16" height="16" viewBox="0 0 16 16"><circle cx="7" cy="7" r="5" fill="none" stroke="#5c6166" stroke-width="2"/><path d="M10.5 10.5l4 4" stroke="#5c6166" stroke-width="2.4"/><circle cx="7" cy="7" r="2.5" fill="#a9c23f"/></svg>Search Jobs</span>
    <span>|</span>
    <span><svg width="18" height="14" viewBox="0 0 18 14"><path d="M4 12a3.5 3.5 0 010-7 5 5 0 019.5 1A3 3 0 0114 12z" fill="#5c6166"/><path d="M9 11V6M7 8l2-2 2 2" stroke="#fff" stroke-width="1.5" fill="none"/></svg>Upload CV</span>
  </div>
  <div class="abs account-btn" style="left:619px">Candidate</div>
  <div class="abs account-btn" style="left:719px">Clients</div>

  <nav class="abs main-nav">
    <span class="home"><svg width="14" height="13" viewBox="0 0 14 13"><path d="M7 0L0 6h2v7h4V9h2v4h4V6h2z" fill="#fff"/></svg></span>
    <a class="active">Recruiting Services</a>
    <a>HR consulting Services</a>
    <a>Testimonials</a>
    <a>Job Openings</a>
    <a>Job Application</a>
    <span class="site-search">Search site<svg width="12" height="12" viewBox="0 0 12 12"><circle cx="5" cy="5" r="3.8" fill="none" stroke="#5c6166" stroke-width="1.6"/><path d="M8 8l3.5 3.5" stroke="#5c6166" stroke-width="1.8"/></svg></span>
  </nav>
</header>

<section>
  <div class="abs hero" role="img" aria-label="Bright modern office with green walls and two smiling recruiters"></div>
  <div class="abs hero-caption">Bluvanta demonstrated extraordinary insight in understanding both the client recruiting needs and the candidates' objectives"</div>
  <div class="abs hero-arrow" style="left:182px"><svg width="15" height="15" viewBox="0 0 15 15"><path d="M9 4L5.5 7.5 9 11" stroke="#a9c23f" stroke-width="2" fill="none"/></svg></div>
  <div class="abs hero-arrow" style="left:797px"><svg width="15" height="15" viewBox="0 0 15 15"><path d="M6 4l3.5 3.5L6 11" stroke="#a9c23f" stroke-width="2" fill="none"/></svg></div>
</section>

<section>
  <div class="abs intro-rule"></div>
  <div class="abs intro-ring"></div>
  <h1 class="abs heading intro-title">Where strategy meets recruiting</h1>
  <div class="abs intro-copy">
    <p>The modern and successful recruiting leader begins with a strategic foundation, leverages connectivity through social media, stakeholder relationships and builds pipelines of competencies, quickly and flexibly to solve pressing employment challenges.</p>
    <p>Bluvanta combines strategy and action to find top talent in the areas of Engineering, IT, Operations, and Accounting and Administration. Look to Bluvanta to explore new pathways to strategic relevancy.&nbsp; From strategy to execution, we are the team you need… NOW!</p>
    <p>How can we be your strategic partner to success?</p>
  </div>
  <div class="abs small-btn" style="left:754px;top:509px;width:57px">Learn more</div>
</section>

<section class="abs services">
  <div class="abs service" style="left:182px">
    <div class="disc"><svg width="44" height="30" viewBox="0 0 44 30"><circle cx="15" cy="9" r="6" fill="#fff"/><path d="M3 29c0-9 5-12 12-12s12 3 12 12z" fill="#fff"/><circle cx="29" cy="9" r="6" fill="#dcdedf"/><path d="M26 17c8 0 15 3 15 12H30c0-6-2-9-4-12z" fill="#dcdedf"/></svg></div>
    Expert Recruiting
  </div>
  <div class="abs service" style="left:397px">
    <div class="disc"><svg width="40" height="26" viewBox="0 0 40 26"><rect x="2" y="6" width="17" height="17" rx="2" fill="#dcdedf"/><rect x="21" y="3" width="17" height="17" rx="2" fill="#fff"/><circle cx="20" cy="14" r="3.5" fill="#fff"/></svg></div>
    Recruiting Strategy
  </div>
  <div class="abs service" style="left:614px">
    <div class="disc on"><svg width="32" height="38" viewBox="0 0 32 38"><circle cx="16" cy="11" r="8" fill="#4a4f54"/><path d="M2 38c0-12 6-17 14-17s14 5 14 17z" fill="#4a4f54"/></svg></div>
    Human Resource Consulting
  </div>
</section>

<section class="abs numbers">
  <div class="numbers-head heading">Here at Bluvanta, we love our numbers!</div>
  <div class="abs stat" style="top:46px;height:33px"><span class="num">8</span><span class="txt">is symbolized for the beginning (7 days of creation), success, balance, 'giving and receiving' and the number of 'Karma'. <u><strong>To Bluvanta… it means that and more!</strong></u></span></div>
  <div class="abs stat" style="top:86px;height:35px"><span class="num">96%</span><span class="txt">is the success rate of our direct hire placements for 12 months or longer. We offer 90-day guarantees and stand behind the quality of our placements.</span></div>
  <div class="abs stat" style="top:127px;height:34px"><span class="num">98%</span><span class="txt">of our clients have continued to give us repeat business and 90% of our customers come from referral business.</span></div>
  <div class="abs stat" style="top:168px;height:27px"><span class="num">3-14</span><span class="txt">days it takes us to find you great top talent for your critical and challenging job openings.</span></div>
  <div class="abs scroll"></div>
</section>

<aside class="abs testimonials">
  <h2>Testimonials</h2>
  <div class="quote">"What differentiates Bluvanta from other HR service firms is their desire to find the right HR solutions for your unique company culture"</div>
  <cite>ABC, Architecture Firm</cite>
  <div class="quote" style="border-top:1px dotted #bbb;padding-top:7px">"Personal attention sets you apart from the rest. You took the time to really listen to my career goals and made me feel worthy and respected"</div>
  <cite>Dana, Candidate</cite>
  <div class="small-btn" style="width:84px;margin-left:88px">More Testimonials</div>
</aside>

<div class="abs social-tab"><i></i><i></i><i></i><i></i><i></i><i></i></div>
<div class="abs band"></div>

<footer class="abs footer">
  <div class="abs" style="left:190px;top:22px;width:105px">
    <h3>About Bluvanta</h3>
    <ul><li>About Us</li><li>What we do</li><li>How we do</li><li>Testimonials</li><li>Our awards</li></ul>
  </div>
  <div class="abs" style="left:317px;top:22px;width:135px">
    <h3>Contact Us</h3>
    <div class="contact-row"><svg width="10" height="13" viewBox="0 0 10 13"><path d="M5 0a5 5 0 00-5 5c0 4 5 8 5 8s5-4 5-8a5 5 0 00-5-5z" fill="#fff"/><circle cx="5" cy="5" r="2" fill="#8fa336"/></svg><span>Bluvanta<br>2280 Larkspur Avenue<br>Suite 310<br>Houston, TX, 77019</span></div>
    <div class="contact-row"><svg width="12" height="12" viewBox="0 0 12 12"><circle cx="6" cy="6" r="5" fill="none" stroke="#fff" stroke-width="1.5"/><path d="M1 6h10M6 1c-3 3-3 7 0 10M6 1c3 3 3 7 0 10" stroke="#fff" fill="none"/></svg><span>www.bluvantatalent.com</span></div>
    <div class="contact-row"><svg width="13" height="10" viewBox="0 0 13 10"><rect x=".5" y=".5" width="12" height="9" fill="none" stroke="#fff"/><path d="M.5.5l6 5 6-5" stroke="#fff" fill="none"/></svg><span>info@bluvantatalent.com</span></div>
    <div class="contact-row big"><svg width="13" height="13" viewBox="0 0 13 13"><path d="M3 0l2 3-1.5 1.5a8 8 0 005 5L10 8l3 2-1.5 3C6 13 0 7 0 1.5z" fill="#fff"/></svg><span>555.201.4830</span></div>
    <div class="contact-row big"><svg width="14" height="12" viewBox="0 0 14 12"><rect x="3" y="0" width="8" height="4" fill="#fff"/><rect x="0" y="4" width="14" height="6" fill="#fff"/><rect x="3" y="8" width="8" height="4" fill="#dfe5c2"/></svg><span>555.201.4831</span></div>
  </div>
</footer>
<div class="abs badge"></div>
<div class="abs hub">Certified Supplier</div>

<aside class="abs jobs">
  <div class="jobs-head"><span>Job Openings</span><svg width="18" height="11" viewBox="0 0 18 11"><circle cx="4.5" cy="6.5" r="4" fill="#fff"/><circle cx="13.5" cy="6.5" r="4" fill="#fff"/><rect x="7" y="2" width="4" height="4" fill="#fff"/></svg></div>
  <ul>
    <li>- Halvard is hiring</li>
    <li>- Northwind is looking for a decent Art director</li>
    <li>- Corvex is hiring developer</li>
    <li>- Northwind is looking for a decent designer</li>
  </ul>
  <div class="small-btn" style="width:84px;margin:6px auto 0">More Vacancies</div>
</aside>

<aside class="abs fan">
  <div class="fan-name"><span>Bluvanta</span><i></i><span class="follow">Follow</span></div>
  <div style="border-top:1px solid #ddd;margin-top:6px;padding-top:6px">8,046 people like <b style="color:#3b5a9a">Bluvanta</b></div>
  <div class="thumbs" role="img" aria-label="Grid of follower profile photos"><div></div><div></div><div></div><div></div><div></div><div></div><div></div><div></div></div>
  <div style="border-top:1px solid #ddd;margin-top:10px;padding-top:4px;color:#666">Social plugin</div>
</aside>

<div class="abs copyright">Copyright © 2013 Bluvanta&nbsp; All rights reserved.&nbsp; /&nbsp;&nbsp; Site Map&nbsp; /&nbsp;&nbsp; Disclaimers</div>
</body>
</html>
```